Bicycle tour magazine

Actually, it's not a magazine. But I'd like it to look like one.

We have a bicycle tour. People who do these bicycle tours are given a 10-12 page packet outlining the day-to-day itinerary and explaining what they will see. We've been using the same (boring) Word template for 5 years now and need to update this to look more professional.

We have three different tours, but this first project is for one tour (basically the information on the attached PDF)

The magazine will have these different sections:
a. Why this tour
b. Preparing for this tour (which will contain: short texts on "What to pack", "How to train", etc.
c. Day 1, 2, 3, 4, 5, 6, 7, 8, 9, 10
Each of the above "Days" will have very short "articles" like:
"The numbers"
(the kilometers ridden, the meters climbed, etc)

"The Route"
Navigation directions...be careful turning here, etc.

"Points of Interest"
What they will be seeing today

"Where to Eat",
Suggestions on where to eat

"The Hotel"
A bit of information about the hotel

Target Market(s)

English speaking cyclists...UPSCALE.

Industry/Entity Type

Tour

Font styles to use
Sans Serif

Colors
f04a50

Requirements
Must have
• 1. take the information on the PDF update the layout using a more advanced template (illustrator ? photoshop ?)
• 2. New PDF should come in three versions:
• a. version suitable for computer viewing
• b. version suitable for laser printer
• c. version suitable for press printing (if we decide to go that route)
• 3. New design should look like a magazine page, with headers, etc. Pleases include attached map and add your own generic pictures (two or three ) as I would like to have pictures of scenery shown on these pages.
• 4. The attached pdf includes the information that has been present until now. However, since we're making this information look like a magazine, I imagine that we'll be using space much differently....making it feel lighter, less dense. etc.
• Please google "Pedalvorna" to see company website.
• Photos at: https://www.snapmurel.com/photos/pedalvorna/collections/48302916673051824/
Nice to have
• Ideally, the person doing this project will also have experience with ibook and kindle OS, as we would eventually like these PDFs to have an electronic book format and made available on these platforms.
• Here are some templates I like:
• http://layoutbrook.net/item/minimal-magazine-3/5184027?WT.oss_phrase=&WT.oss_rank=33&WT.z_author=TalbotFenn&WT.ac=search_thumb
• http://layoutbrook.net/item/indesign-magazine-template/3829461?WT.oss_phrase=&WT.oss_rank=207&WT.z_author=kelvadro&WT.ac=search_thumb
• http://layoutbrook.net/item/elegant-art-magazine-template/640357?
• WT.oss_phrase=Magazine%20template&WT.oss_rank=22&WT.z_author=studioMarwickel&WT.ac=search_thumb

```html
<!DOCTYPE html>
<html lang="en">
<head>
<meta charset="utf-8">
<title>Why This Tour</title>
<link rel="stylesheet" href="https://fonts.googleapis.com/css2?family=Oswald:wght@700&family=Noto+Serif:wght@400&display=swap">
<style>
  :root {
    --backdrop: #e4e4e4;
    --paper: #ffffff;
    --ink: #1a1a1a;
    --accent: #f04a50;
    --sky: #3f86dc;
    --sky-light: #b9d6f2;
    --field: #6f9a3c;
    --field-dark: #4d6e2a;
    --road: #c8c4bc;
    --jersey: #d9484c;
  }
  * { box-sizing: border-box; margin: 0; padding: 0; }
  html, body { width: 1200px; height: 800px; overflow: hidden; background: var(--backdrop); }
  .spread {
    position: absolute; left: 50px; top: 33px;
    width: 1100px; height: 734px;
    display: flex;
    box-shadow: 0 10px 30px rgba(0,0,0,0.18);
  }
  .page { position: relative; width: 550px; height: 734px; background: var(--paper); overflow: hidden; }
  .page--left::after {
    content: ""; position: absolute; top: 0; right: 0; width: 40px; height: 100%;
    background: linear-gradient(to right, rgba(0,0,0,0), rgba(0,0,0,0.12));
    pointer-events: none;
  }
  .photo { position: absolute; }
  .photo--vineyard {
    left: 0; top: 0; width: 300px; height: 380px;
    background: linear-gradient(180deg, var(--sky) 0%, var(--sky-light) 30%, #9fb8c9 42%, var(--field-dark) 55%, var(--field) 70%, #b8aa92 100%);
  }
  .photo--rider {
    left: 268px; top: 452px; width: 172px; height: 270px;
    background: linear-gradient(180deg, var(--sky-light) 0%, #e9eef2 25%, var(--field) 45%, var(--jersey) 62%, #c7b79a 100%);
  }
  .photo--road {
    inset: 0;
    background: linear-gradient(180deg, #1f63d6 0%, var(--sky) 25%, #8fc0ee 40%, var(--field) 44%, var(--field-dark) 55%, #a8a49a 62%, var(--road) 100%);
  }
  .column {
    position: absolute; left: 318px; top: 18px; width: 212px;
    font-family: "Noto Serif", serif; font-size: 10px; line-height: 13.5px;
    color: var(--ink); text-align: justify; hyphens: auto;
  }
  .column p + p { margin-top: 7px; }
  .headline {
    position: absolute; left: 20px; top: 392px; width: 240px;
    font-family: "Oswald", sans-serif; font-weight: 700; text-transform: uppercase;
  }
  .headline__lead { display: block; font-size: 92px; line-height: 88px; color: var(--ink); letter-spacing: -1px; }
  .headline__tail { display: block; font-size: 42px; line-height: 46px; color: var(--accent); }
  .intro {
    position: absolute; left: 20px; top: 545px; width: 232px; height: 175px;
    column-count: 2; column-gap: 10px;
    font-family: "Noto Serif", serif; font-size: 10.5px; line-height: 13.5px;
    color: var(--ink); text-align: justify; hyphens: auto;
  }
  .intro p + p { margin-top: 6px; }
  .dropcap {
    float: left; font-family: "Oswald", sans-serif; font-weight: 700;
    font-size: 44px; line-height: 38px; margin: 2px 4px 0 0; color: var(--ink);
  }
  .folio {
    position: absolute; left: 12px; bottom: 8px;
    font-family: "Noto Serif", serif; font-size: 7px; color: var(--ink);
  }
</style>
</head>
<body>
  <main class="spread">
    <section class="page page--left">
      <div class="photo photo--vineyard" role="img" aria-label="Cyclists in red jerseys riding a gravel lane through a hillside vineyard under a cloudy blue sky"></div>

      <div class="column">
        <p>Ten days of quiet roads, vineyard climbs and lakeside towns give this tour its rhythm. Each morning starts with coffee and a short briefing, then the group rolls out at its own pace. Support vans carry luggage, spare parts and snacks, so riders carry only what they need for the day.</p>
        <p>The route follows farm lanes and river paths away from heavy traffic. Climbs are steady rather than steep, and every stage ends early enough to walk through town before dinner. Guides know the local cafes, the best viewpoints and the bakeries worth a stop.</p>
        <p>Hotels are small, family run and chosen for comfort. Rooms are quiet, bikes are stored safely overnight, and breakfast is generous. Riders of most levels finish the tour stronger than they began, with stories to share long after the last kilometre.</p>
        <p>Expect long lunches, clear mountain air and evenings on a terrace watching the light fade over the hills. This is cycling at a relaxed, generous pace.</p>
      </div>

      <h1 class="headline">
        <span class="headline__lead">Why</span>
        <span class="headline__tail">This Tour</span>
      </h1>

      <div class="intro">
        <p><span class="dropcap">F</span>ew places in Europe reward a cyclist the way this country does. The roads are smooth, drivers are patient and the scenery changes every hour, from vineyards to orchards to alpine pastures and clear lakes.</p>
        <p>Our guides ride with you, share the history of each valley and make sure the day unfolds without worry. All you need to do is pedal and enjoy.</p>
      </div>

      <div class="photo photo--rider" role="img" aria-label="Cyclist in a pink jersey pausing with a red road bike beside fields, another rider behind"></div>

      <span class="folio">4</span>
    </section>

    <section class="page page--right">
      <div class="photo photo--road" role="img" aria-label="Group of cyclists riding along a narrow paved country road between green fields under a deep blue summer sky"></div>
    </section>
  </main>
</body>
</html>
```